Award-winnning Estate Agent needs a premium version of their 'For Sale' board design

We need a premium option for our 'For Sale' board design. We have a standard board that is attached to this brief, but were are looking to have a premium design version that we will use when selling exclusive properties. Our company name is Harbourline Vale Estates and the name for this is exclusive selection is: 'The Harbourline Collection'. The design needs to work with our current brand, but have a distinctive PREMIUM feel to it. I have uploaded the barnd guidelines and also some of the exisisting logo variations. We do NOT need a new logo but feel free to play around with colours, fonts, sizes etc. for the sign.

Target Market(s)

Property buyers & house hunters

Industry/Entity Type

Real Estate - Residential Property

Font styles to use
Sans Serif

Requirements
Must have
• A premium fee, must be square design, must be easy to read when driving past the sign
Nice to have
• I'm open ot ideas

```html
<!DOCTYPE html>
<html lang="en">
<head>
<meta charset="utf-8">
<title>Harbourline Vale Estates – For Sale Board</title>
<link rel="stylesheet" href="https://fonts.googleapis.com/css2?family=Tinos:wght@700&display=swap">
<style>
  :root {
    --board: #e8e8e8;
    --gold: #c4a265;
    --gold-light: #e3d3b3;
    --ink: #000000;
    --white: #ffffff;
  }
  html, body {
    margin: 0;
    padding: 0;
    width: 1200px;
    height: 1199px;
    overflow: hidden;
    background: var(--board);
  }
  .board {
    position: relative;
    width: 1200px;
    height: 1199px;
    background: var(--board);
    font-family: "Tinos", "Times New Roman", serif;
    font-weight: 700;
    overflow: hidden;
  }
  .board-shapes {
    position: absolute;
    inset: 0;
  }
  .collection-title {
    position: absolute;
    top: 66px;
    left: 0;
    width: 100%;
    margin: 0;
    text-align: center;
    color: var(--gold);
    font-size: 50px;
    letter-spacing: 1px;
    text-transform: uppercase;
    line-height: 1;
  }
  .headline {
    position: absolute;
    top: 128px;
    left: 0;
    width: 100%;
    margin: 0;
    text-align: center;
    color: var(--ink);
    font-size: 168px;
    letter-spacing: 2px;
    line-height: 1;
  }
  .agency-mark {
    position: absolute;
    top: 360px;
    left: 0;
    width: 100%;
    display: flex;
    flex-direction: column;
    align-items: center;
    gap: 34px;
  }
  .agency-dot {
    width: 150px;
    height: 150px;
    border-radius: 50%;
    background: var(--gold);
  }
  .agency-name {
    margin: 0;
    color: var(--ink);
    font-size: 58px;
    letter-spacing: 4px;
    text-transform: uppercase;
    line-height: 1;
  }
  .contact {
    position: absolute;
    left: 0;
    width: 100%;
    text-align: center;
    color: var(--white);
    margin: 0;
    line-height: 1;
  }
  .contact-phone {
    top: 790px;
    font-size: 98px;
    letter-spacing: 1px;
  }
  .contact-web {
    top: 920px;
    font-size: 52px;
  }
</style>
</head>
<body>
<main class="board">
  <svg class="board-shapes" width="1200" height="1199" viewBox="0 0 1200 1199" aria-hidden="true">
    <!-- side rails -->
    <g class="side-rail" fill="var(--gold-light)">
      <rect x="8" y="0" width="12" height="960"/>
      <rect x="1180" y="0" width="12" height="960"/>
      <rect x="20" y="140" width="50" height="12"/>
      <rect x="20" y="345" width="50" height="12"/>
      <rect x="20" y="550" width="50" height="12"/>
      <rect x="20" y="755" width="50" height="12"/>
      <rect x="1130" y="140" width="50" height="12"/>
      <rect x="1130" y="345" width="50" height="12"/>
      <rect x="1130" y="550" width="50" height="12"/>
      <rect x="1130" y="755" width="50" height="12"/>
    </g>
    <!-- gold base -->
    <polygon class="base-band" fill="var(--gold)" points="0,935 600,1178 1200,935 1200,1199 0,1199"/>
    <!-- contact banner -->
    <polygon class="contact-banner" fill="var(--ink)" points="112,720 1098,720 1098,920 600,1113 112,950"/>
    <line class="contact-rule" x1="190" y1="898" x2="1020" y2="890" stroke="var(--gold)" stroke-width="3"/>
    <!-- phone badge -->
    <g class="phone-badge">
      <circle cx="604" cy="700" r="44" fill="var(--gold)" stroke="var(--board)" stroke-width="6"/>
      <path d="M590 680 c-4 3 -6 8 -3 15 c4 10 12 19 22 24 c7 3 12 1 15 -3 l3 -4 c1 -2 0 -4 -2 -5 l-8 -5 c-2 -1 -4 0 -5 1 l-3 3 c-6 -3 -11 -8 -14 -14 l3 -3 c1 -1 2 -3 1 -5 l-5 -8 c-1 -2 -3 -3 -5 -2 z" fill="var(--white)"/>
    </g>
  </svg>

  <p class="collection-title">The Harbourline Collection</p>
  <h1 class="headline">FOR SALE</h1>

  <div class="agency-mark">
    <span class="agency-dot"></span>
    <p class="agency-name">Harbourline Vale Estates</p>
  </div>

  <p class="contact contact-phone">01632 960418</p>
  <p class="contact contact-web">harbourlinevaleestates.co.uk</p>
</main>
</body>
</html>
```